Mobile Repair Service on location needs a Web Design

We are starting a new mobile device repair service called Handset Haven and our website needs a design!

Hello Designers!
First, we'd like to make clear this is more than a simple web design contest, we want the designers to create an idea. We want someone who can create the whole theme of the service's we provide. We want someone that can help design our visual branding, help us communicate a sentiment. And we are willing to pay for that.

Who are we?
Our company is based in Rotterdam, the Netherlands. We provide different services for all kinds of electronic devices. The kind of services we provide are, among other things, installations of hardware and software and the repair of broken or malfunctioning devices.
We are starting a new service that offers mobile device repairs on location, be it at the home of our customers, their office, or any other place. Just give us the address and we will come to you for the repair job. This is also our main USP. We have multiple skilled engineers who drive trough the country on a daily basis and can be on location within a working day. Repair is done immediately onsite while the customer waits. At this stage we will start with the smartphone product-group within the mobile devices. In a second phase we might also add tablets.
People don't want to be without their phone for weeks because of some parts that needed to be ordered by a repair center they had to sent their phone to. We offer a fully functional mobile repair center in the form of specially customized vans. These vans have all the tools and utilities needed by our engineers to safely repair your mobile device. Your phone is being repaired directly in front of you, the next business-day, on a location you desire.

For this new service we are creating a website called Handset Haven. The website needs a story and matching design and this is where you come in. We are not looking for a simple template design we can get from any place. We need a story. We want you to create an idea, build a unique theme or vision that helps sell the product/service. This goes beyond the design of the website. We need the whole package, the design you are creating needs to have returning elements like icons, color use, images, maybe even characters etc. You name it! There needs to be a common thread in the design so we can reuse elements in, for example, the email templates, the work order or receipt we give to our customers (we may contact the winner of the contest to design these for us as well!).

The name 'Handset Haven' is chosen. Rehab (short for rehabilitate) has a bold and playful tone to it and the design needs to reflect the name. So we're looking for a somewhat playful and cheeky design. Definitely not too serious and definitely modern. We already got a logo that we love and that fit's this description (see attached design documents for the logo). It's bold, powerful and fun. Our web design needs to reflect this as well and has to fit in with our logo.
We would really like it if the design somehow incorporates elements that highlight our unique selling points (repairs on location, we come to you etc.). We would really like some form of story telling in the design. Think clumsy people breaking their phones. Teenagers in tears because they have no access to their friends. People nowadays have the need to always be 'connected'. What happens when your phone is broken or malfunctioning? We're handling tech, we are nerds and a little bit weird, but we're professionals and here to help you with your problem. The sentiment Byte Brigade tries to communicate is something we really like. We're looking for fresh idea's, anything goes!

In an overview all Unique Selling Points of the Handset haven service:
- Professional service on location. Don’t ship to us we will come to you!
- Clear pricing upfront. No hidden cost.
- Next business-day repair.
- Backed by a professional call center open 12 hours a day and open on a Saturday as well
- Backed by a professional repair center with more then 12 years of experience
- Repair is done by certified engineers
- 1 year warranty on the repair

The process:
The main function of our website will be for customers to make a repair request. A customer will visit our website and can make a repair request immediately by going through a 'request-order-flow'. In this flow he or she will need to fill in some forms and can select wich type/model/brand of mobile device he or she has and what parts need to be repaired. After a request is placed we will call the customer back (within an hour) for a short intake and to set a date/time and location. Our engineer will meet the customer at the specified location and will repair the device onsite in one of our mobile repair centers, which is a specialized van equipped with all the tools needed for device restorations.
So in short the steps are:
- Choose your device and repair job
- Place the order
- Get a callback within the hour
- Set date and location
- We will come to you.

Website functionality:
Our website is our main form of communication. So the sentiment we want to communicate needs be reflected in the design. We need a main/front page designed (preferably a long scrolling page design) containing:
1. Customers will be able to request a repair job directly on our website. So there will need to be a prominent button/link at the top of our main page that will bring the customer to this 'request-order-flow'. This is the main flow which needs to be full focus on the front page. All other items are secondary.
2. The general information of who we are and what we do, and why the customer should choose us. Preferably in short bullet-point type keywords/sentences with icons or other visual cues. See our unique selling points to get an idea of the information that will be displayed here.
3. There needs to be a section that will explain the process (see above) of a repair request step-by- step, again in brief short key sentences and with (custom) icons.
4. There needs to be a section that explains to the customer he/she can always contact us if they are not sure what the problem is with their device, and for this reason are not sure what repair request they should order.
5. We want to implement some functionality that display customer ratings or customer reviews. So there needs to be room for some kind of widget of plugin we're going to implement which shows these reviews.
6. A 'For business section' where we will explain all the options we provide for corporate clients.
7. Social media links.
8. There needs to be a menu with buttons that leads to the all sections described in the previous points.

For now, we need a design for our front page. In the second phase, when we have picked our winner, we may ask the winner to design the page(s) for our request workflow as well.

EDIT:
Finally, we have a very specific order in mind for the different segments of our website. We would like you to add some more segments that were not in our original brief as well:

1. Top header with order/request button. (should instantly make clear our main USP, we do repairs on location)
2. Our process
3. Our unique selling points / why choose us
4. The kind of repairs we do (broken screens, broken batteries, water damage, broken camera's, no sound etc.)
5. A 'meet our team' section, where we introduce some of our engineers
6. A 'contact us for any questions' section/
7. Testimonials/user reviews
8. A section where we show key performance indicators
9. 'For businesses' sections
10.'Subscribe for newsletter' field
11. Social media buttons

Industry/Entity Type

It Service

Number of Pages Required

1 page

Font styles to use
Sans Serif

Requirements
Must have
• a main/front page, design only
• custom icons/images for banners, adverts online and in print (high res)
Nice to have
• Storytelling in our design.
• Design that fits with our brand new logo.
• Elements like icons to have a flat design.
• Keep in mind that the website will need to be responsive when designing! (Ideally provide an example of the mobile design as well)
• Create a fun and trustworthy feeling.

```html
<!DOCTYPE html>
<html lang="en">
<head>
<meta charset="utf-8">
<title>Handset Haven – Mobile repair on location</title>
<link href="https://fonts.googleapis.com/css2?family=Open+Sans:wght@400;600;700;800&display=swap" rel="stylesheet">
<style>
:root{
  --orange:#f26522;
  --orange-dark:#d9531a;
  --ink:#333333;
  --muted:#777777;
  --line:#e3e3e3;
  --blush:#fdf1eb;
  --grey-bg:#f4f4f4;
  --white:#ffffff;
  --footer-bar:#f0f0f0;
}
*{box-sizing:border-box;margin:0;padding:0}
html,body{width:1200px;height:4204px;overflow:hidden}
body{font-family:'Open Sans',Arial,sans-serif;color:var(--ink);background:var(--white);font-size:13px;line-height:1.6}
.section-title{text-align:center;color:var(--orange);font-size:26px;font-weight:700;letter-spacing:.5px}
.title-rule{width:60px;height:2px;background:var(--orange);margin:10px auto 0}
.btn{display:inline-block;background:var(--orange);color:var(--white);font-weight:600;font-size:13px;padding:11px 22px;border-radius:2px}

/* header */
.site-header{height:56px;display:flex;align-items:center;justify-content:space-between;padding:0 100px}
.brand{display:flex;align-items:center;gap:10px;font-weight:800;font-size:18px;color:var(--ink)}
.brand-mark{width:30px;height:30px;border-radius:50%;background:var(--orange)}
.header-actions{display:flex;align-items:center;gap:20px;font-size:12px}
.cart{color:var(--muted);font-weight:600}
.header-actions .btn{padding:7px 14px;font-size:12px}
.main-nav{height:26px;background:var(--orange);display:flex;justify-content:space-between;padding:0 100px;color:var(--white);font-size:11px;font-weight:600}
.main-nav ul{display:flex;list-style:none;height:100%}
.main-nav li{padding:0 22px;display:flex;align-items:center}
.main-nav li.active{background:var(--orange-dark)}
.main-nav .secondary li{padding:0 12px;border-left:1px solid rgba(255,255,255,.4)}

/* hero */
.hero{position:relative;height:498px}
.hero-photo{position:absolute;inset:0;background:linear-gradient(100deg,#2b2b2b 0%,#4a4a4a 55%,#6d6a66 100%)}
.hero-content{position:relative;padding:126px 0 0 100px;color:var(--white)}
.hero h1{font-size:34px;font-weight:700;letter-spacing:.5px}
.hero h2{font-size:24px;font-weight:700;margin-top:6px}
.hero .ghost-btn{display:inline-block;margin-top:30px;border:2px solid var(--white);padding:9px 18px;font-size:12px;font-weight:700}

/* process */
.process{height:480px;padding-top:48px}
.steps{display:flex;justify-content:space-between;align-items:flex-start;width:1000px;margin:130px auto 0}
.step{width:140px;text-align:center;font-size:13px;font-weight:600}
.step svg{display:block;margin:0 auto 20px}
.step-arrow{margin-top:26px}

/* why */
.why{height:580px;background:var(--blush);padding-top:30px;text-align:center}
.why .lead{font-weight:700;font-size:14px;margin-top:12px}
.why .intro{width:880px;margin:14px auto 0;font-size:12px;color:var(--muted)}
.repairs{display:flex;justify-content:space-between;width:1000px;margin:70px auto 0}
.repair{width:170px}
.repair-icon{width:118px;height:118px;border-radius:50%;border:3px solid var(--orange);background:var(--white);margin:0 auto;display:flex;align-items:center;justify-content:center}
.repair.active .repair-icon{background:var(--orange)}
.repair h3{font-size:14px;font-weight:700;margin-top:26px}
.repair.active h3{color:var(--orange)}
.repair p{font-size:11px;color:var(--muted);margin-top:6px}

/* team */
.team{height:428px;padding-top:38px}
.members{display:flex;justify-content:space-between;width:1000px;margin:70px auto 0}
.member{width:460px}
.member-head{display:flex;align-items:center;gap:22px}
.avatar{width:90px;height:90px;border-radius:50%;border:3px solid var(--orange)}
.avatar.a{background:linear-gradient(160deg,#c9b49f,#6d5a4b)}
.avatar.b{background:linear-gradient(160deg,#e2c7a5,#9a7c5f)}
.member h3{font-size:18px;font-weight:600}
.member .role{color:var(--orange);font-size:12px}
.member p{font-size:12px;color:var(--muted);margin-top:26px}

/* contact */
.contact{height:392px;background:var(--grey-bg);position:relative}
.contact-text{position:absolute;left:100px;top:58px;width:500px}
.contact h2{color:var(--orange);font-size:24px;font-weight:700}
.contact p{font-size:12px;color:var(--muted);margin-top:14px}
.contact .btn{margin-top:28px;font-size:11px}
.contact-photo{position:absolute;right:0;top:0;width:520px;height:100%;background:linear-gradient(120deg,#e9e7e5,#cfc7c0)}

/* testimonials */
.testimonials{height:420px;padding-top:62px;position:relative}
.quotes{display:flex;justify-content:space-between;width:960px;margin:62px auto 0}
.quote{width:290px;position:relative;text-align:center}
.quote-box{border:2px solid var(--orange);padding:34px 22px 22px;font-size:12px;color:var(--muted);height:160px;background:var(--white)}
.quote.featured .quote-box{background:var(--orange);color:var(--white);height:176px;margin-top:-8px}
.quote-badge{position:absolute;left:50%;top:-16px;margin-left:-16px;width:32px;height:32px;border-radius:50%;background:var(--orange);border:2px solid var(--white)}
.quote.featured .quote-badge{top:-24px;background:var(--white);border-color:var(--orange)}
.quote cite{display:block;margin-top:20px;font-style:normal;color:var(--orange);font-size:12px}
.slider-arrow{position:absolute;top:276px}
.slider-arrow.left{left:34px}
.slider-arrow.right{right:34px}

/* kpi */
.kpi{height:464px;position:relative;border-top:1px solid var(--line)}
.kpi h2{position:absolute;left:100px;top:40px;color:var(--orange);font-size:26px;font-weight:700}
.kpi-list{position:absolute;left:100px;top:110px;list-style:none;width:440px}
.kpi-list li{display:flex;align-items:center;gap:22px;font-size:12px;margin-bottom:22px}
.kpi-list svg{flex:none}
.kpi .btn{position:absolute;left:160px;top:386px;font-size:12px}
.kpi-photo{position:absolute;right:0;top:60px;width:560px;height:340px;background:linear-gradient(130deg,#f3f1ef,#cfd4d8 60%,#9aa2a8)}

/* business */
.business{height:480px;background:linear-gradient(160deg,#f47a3c,var(--orange) 60%,#e85a1b);color:var(--white);text-align:center;padding-top:64px}
.business .section-title{color:var(--white)}
.business .title-rule{background:var(--white)}
.biz-cols{display:flex;justify-content:space-between;width:880px;margin:44px auto 0;text-align:left}
.biz-cols ul{list-style:none;width:420px}
.biz-cols li{font-size:12px;padding-left:22px;position:relative;margin-bottom:10px}
.biz-cols li::before{content:"";position:absolute;left:0;top:5px;width:9px;height:9px;background:var(--white)}
.business .white-btn{display:inline-block;margin-top:46px;background:var(--white);color:var(--ink);font-weight:700;font-size:12px;padding:12px 22px}

/* footer */
.site-footer{height:300px;display:flex;padding:48px 100px 0;gap:60px}
.footer-brand{width:190px;display:flex;align-items:flex-start;gap:10px;font-weight:800;font-size:22px;line-height:1.1}
.footer-brand .brand-mark{width:40px;height:40px;flex:none}
.footer-col h4{color:var(--orange);font-size:13px;font-weight:700;margin-bottom:14px}
.footer-col.orders{width:200px}
.footer-col.contactus{width:200px}
.footer-col ul{list-style:none;font-size:11px;color:var(--muted)}
.footer-col li{margin-bottom:4px;padding-left:12px;position:relative}
.footer-col li::before{content:"›";position:absolute;left:0;color:var(--orange)}
.contact-item{display:flex;gap:10px;font-size:11px;color:var(--muted);margin-bottom:12px}
.contact-item b{color:var(--ink);display:block}
.newsletter input{width:220px;height:32px;border:1px solid var(--line);padding:0 10px;font-family:inherit;font-size:11px}
.newsletter .btn{margin-top:12px;font-size:11px;padding:8px 14px}
.footer-bar{height:44px;background:var(--footer-bar);display:flex;align-items:center;justify-content:space-between;padding:0 100px;font-size:11px;color:var(--muted)}
.socials{display:flex;gap:8px}
.socials span{width:22px;height:22px;border-radius:50%;border:1px solid #999}
</style>
</head>
<body>

<header class="site-header">
  <div class="brand"><span class="brand-mark"></span>Handset Haven</div>
  <div class="header-actions">
    <span class="cart">CART: 0 items</span>
    <span class="btn">Request Order Flow</span>
  </div>
</header>
<nav class="main-nav">
  <ul><li class="active">PRODUCTS</li><li>BRANDS</li><li>DEALS</li></ul>
  <ul class="secondary"><li>Weekly Ad</li><li>Deal of the Day</li><li>Gift Cards</li><li>Gift Ideas &amp; Registry</li></ul>
</nav>

<section class="hero">
  <div class="hero-photo" role="img" aria-label="Photo of a person holding a smartphone with a cracked screen"></div>
  <div class="hero-content">
    <h1>PROFESSIONAL SERVICE ON LOCATION</h1>
    <h2>DON'T SHIP TO US WE WILL COME TO YOU!</h2>
    <span class="ghost-btn">1 YEAR WARRANTY ON REPAIR</span>
  </div>
</section>

<section class="process">
  <h2 class="section-title">OUR PROCESS</h2>
  <div class="title-rule"></div>
  <div class="steps">
    <div class="step">
      <svg width="56" height="70" viewBox="0 0 56 70"><path d="M28 68C28 68 4 40 4 26a24 24 0 0 1 48 0c0 14-24 42-24 42z" fill="none" stroke="#bbb" stroke-width="2"/><rect x="20" y="12" width="16" height="26" rx="2" fill="none" stroke="#f26522" stroke-width="2.5"/><circle cx="28" cy="34" r="1.5" fill="#f26522"/></svg>
      Choose your device and repair job</div>
    <svg class="step-arrow" width="40" height="20" viewBox="0 0 40 20"><path d="M2 10h32M26 3l8 7-8 7" fill="none" stroke="#ccc" stroke-width="2"/></svg>
    <div class="step">
      <svg width="56" height="70" viewBox="0 0 56 70"><path d="M28 68C28 68 4 40 4 26a24 24 0 0 1 48 0c0 14-24 42-24 42z" fill="none" stroke="#bbb" stroke-width="2"/><path d="M18 26l7 7 13-14" fill="none" stroke="#f26522" stroke-width="3"/></svg>
      Place the order</div>
    <svg class="step-arrow" width="40" height="20" viewBox="0 0 40 20"><path d="M2 10h32M26 3l8 7-8 7" fill="none" stroke="#ccc" stroke-width="2"/></svg>
    <div class="step">
      <svg width="56" height="70" viewBox="0 0 56 70"><path d="M28 68C28 68 4 40 4 26a24 24 0 0 1 48 0c0 14-24 42-24 42z" fill="none" stroke="#bbb" stroke-width="2"/><path d="M19 15c2-2 4-2 5 0l2 4c1 2 0 3-1 4 1 3 3 5 6 6 1-1 2-2 4-1l4 2c2 1 2 3 0 5-6 5-25-13-20-20z" fill="#f26522"/></svg>
      Get a callback within the hour</div>
    <svg class="step-arrow" width="40" height="20" viewBox="0 0 40 20"><path d="M2 10h32M26 3l8 7-8 7" fill="none" stroke="#ccc" stroke-width="2"/></svg>
    <div class="step">
      <svg width="56" height="70" viewBox="0 0 56 70"><path d="M28 68C28 68 4 40 4 26a24 24 0 0 1 48 0c0 14-24 42-24 42z" fill="none" stroke="#bbb" stroke-width="2"/><rect x="16" y="15" width="24" height="22" rx="2" fill="none" stroke="#f26522" stroke-width="2.5"/><path d="M16 22h24M22 12v6M34 12v6" stroke="#f26522" stroke-width="2.5"/></svg>
      Set date and location</div>
    <svg class="step-arrow" width="40" height="20" viewBox="0 0 40 20"><path d="M2 10h32M26 3l8 7-8 7" fill="none" stroke="#ccc" stroke-width="2"/></svg>
    <div class="step">
      <svg width="56" height="70" viewBox="0 0 56 70"><path d="M28 68C28 68 4 40 4 26a24 24 0 0 1 48 0c0 14-24 42-24 42z" fill="none" stroke="#bbb" stroke-width="2"/><path d="M28 40s-9-10-9-16a9 9 0 0 1 18 0c0 6-9 16-9 16z" fill="#f26522"/><circle cx="28" cy="24" r="3" fill="#fff"/></svg>
      We will come to you</div>
  </div>
</section>

<section class="why">
  <h2 class="section-title">WHY CHOOSE US</h2>
  <div class="title-rule"></div>
  <p class="lead">The kind of repairs we do</p>
  <p class="intro">Our company is based in Rotterdam, the Netherlands. We provide different services for all kinds of electronic devices. The kind of services we provide are, among other things, installations of hardware and software and the repair of broken or malfunctioning devices. We are starting a new service that offers mobile device repairs on location, be it at the home of our customers, their office, or any other place.</p>
  <div class="repairs">
    <div class="repair">
      <div class="repair-icon"><svg width="50" height="60" viewBox="0 0 50 60"><rect x="12" y="4" width="26" height="50" rx="4" fill="none" stroke="#f26522" stroke-width="3"/><path d="M18 16l8 8-4 6 8 8" fill="none" stroke="#f26522" stroke-width="2"/></svg></div>
      <h3>Broken Screens</h3><p>Cracked glass or dead touch, we swap the screen on the spot.</p>
    </div>
    <div class="repair active">
      <div class="repair-icon"><svg width="50" height="60" viewBox="0 0 50 60"><rect x="12" y="4" width="26" height="50" rx="4" fill="none" stroke="#fff" stroke-width="3"/><rect x="19" y="18" width="12" height="22" fill="none" stroke="#fff" stroke-width="2"/><path d="M22 15h6" stroke="#fff" stroke-width="2"/></svg></div>
      <h3>Broken Batteries</h3><p>Your phone is dying fast? New battery fitted right in front of you.</p>
    </div>
    <div class="repair">
      <div class="repair-icon"><svg width="50" height="60" viewBox="0 0 50 60"><rect x="12" y="4" width="26" height="50" rx="4" fill="none" stroke="#f26522" stroke-width="3"/><path d="M25 18s-7 9-7 13a7 7 0 0 0 14 0c0-4-7-13-7-13z" fill="#f26522"/></svg></div>
      <h3>Water Damage</h3><p>The next business day, on a location you desire.</p>
    </div>
    <div class="repair">
      <div class="repair-icon"><svg width="50" height="60" viewBox="0 0 50 60"><rect x="12" y="4" width="26" height="50" rx="4" fill="none" stroke="#f26522" stroke-width="3"/><circle cx="25" cy="22" r="6" fill="none" stroke="#f26522" stroke-width="2.5"/><path d="M19 38l12-6" stroke="#f26522" stroke-width="2"/></svg></div>
      <h3>Broken Camera's</h3><p>Blurry or black photos? A new lens module, done while you wait.</p>
    </div>
    <div class="repair">
      <div class="repair-icon"><svg width="50" height="60" viewBox="0 0 50 60"><rect x="12" y="4" width="26" height="50" rx="4" fill="none" stroke="#f26522" stroke-width="3"/><path d="M18 26h4l5-5v16l-5-5h-4z" fill="#f26522"/><path d="M30 25l5 6M35 25l-5 6" stroke="#f26522" stroke-width="2"/></svg></div>
      <h3>No Sound</h3><p>We want you to hear every call, tune and message clearly again.</p>
    </div>
  </div>
</section>

<section class="team">
  <h2 class="section-title">MEET OUR TEAM</h2>
  <div class="title-rule"></div>
  <div class="members">
    <div class="member">
      <div class="member-head"><div class="avatar a" role="img" aria-label="Portrait photo of engineer Ruben Haas"></div><div><h3>Ruben Haas</h3><span class="role">Engineer</span></div></div>
      <p>Ruben has fixed phones for over ten years and drives our northern route. He loves a tricky board repair and always explains what went wrong, so you know how to keep your phone safe next time.</p>
    </div>
    <div class="member">
      <div class="member-head"><div class="avatar b" role="img" aria-label="Portrait photo of engineer Lotte Vermeer"></div><div><h3>Lotte Vermeer</h3><span class="role">Engineer</span></div></div>
      <p>Lotte is our screen and camera expert and covers the Rotterdam area. Calm, quick and precise, she turns a shattered phone into a working one before your coffee has even had time to cool down.</p>
    </div>
  </div>
</section>

<section class="contact">
  <div class="contact-text">
    <h2>CONTACT US FOR ANY QUESTION'S</h2>
    <p>Not sure what is wrong with your device, or which repair you should order? No problem at all. Call or message our team and we will help you find the cause, explain the options and give you a clear price upfront with no hidden costs.</p>
    <p>Our call center is open twelve hours a day and on Saturday as well, so there is always someone ready to listen, answer your question and plan a visit at a time and place that suits you.</p>
    <span class="btn">CONTACT US TODAY</span>
  </div>
  <div class="contact-photo" role="img" aria-label="Photo of a smiling woman holding a smartphone and pointing at it"></div>
</section>

<section class="testimonials">
  <h2 class="section-title">CLIENT TESTIMONIALS</h2>
  <div class="title-rule"></div>
  <svg class="slider-arrow left" width="14" height="24" viewBox="0 0 14 24"><path d="M12 2L2 12l10 10" fill="none" stroke="#999" stroke-width="2"/></svg>
  <svg class="slider-arrow right" width="14" height="24" viewBox="0 0 14 24"><path d="M2 2l10 10L2 22" fill="none" stroke="#999" stroke-width="2"/></svg>
  <div class="quotes">
    <div class="quote"><span class="quote-badge"></span><div class="quote-box">"The engineer came to my office the next morning and my screen was fixed within half an hour. Friendly, fast and a fair price."</div><cite>- Dekker</cite></div>
    <div class="quote featured"><span class="quote-badge"></span><div class="quote-box">"My phone fell in the canal and I thought it was gone. They fixed it on my doorstep and even saved my photos. Great service!"</div><cite>- Ruben Haas</cite></div>
    <div class="quote"><span class="quote-badge"></span><div class="quote-box">"Clear pricing, a quick callback and a new battery while I waited in the van. I will never send my phone away again."</div><cite>- Visser</cite></div>
  </div>
</section>

<section class="kpi">
  <h2>KEY PERFORMANCE INDICATORS</h2>
  <ul class="kpi-list">
    <li><svg width="30" height="30" viewBox="0 0 30 30"><path d="M8 5c2-2 4-2 5 0l2 4c1 2 0 3-1 4 1 3 3 5 6 6 1-1 2-2 4-1l4 2c2 1 2 3 0 5-6 5-25-13-20-20z" fill="#f26522"/></svg>Backed by a professional call center open 12 hours a day and open on a Saturday as well</li>
    <li><svg width="30" height="30" viewBox="0 0 30 30"><path d="M5 25l12-12M17 13l3-8 6 6-8 3" fill="none" stroke="#f26522" stroke-width="3"/></svg>Backed by a professional repair center with more than 12 years of experience</li>
    <li><svg width="30" height="30" viewBox="0 0 30 30"><circle cx="15" cy="11" r="6" fill="#f26522"/><path d="M5 28c0-6 4-10 10-10s10 4 10 10" fill="#f26522"/></svg>Repair is done by certified engineers</li>
    <li><svg width="30" height="30" viewBox="0 0 30 30"><path d="M15 3l10 4v7c0 7-5 11-10 13C10 25 5 21 5 14V7z" fill="#f26522"/><path d="M10 15l4 4 6-7" fill="none" stroke="#fff" stroke-width="2"/></svg>1 year warranty on the repair</li>
  </ul>
  <span class="btn">Next business-day repair</span>
  <div class="kpi-photo" role="img" aria-label="Photo of hands repairing an opened smartphone with tools"></div>
</section>

<section class="business">
  <h2 class="section-title">FOR BUSINESSES</h2>
  <div class="title-rule"></div>
  <div class="biz-cols">
    <ul>
      <li>Professional service on location. Don't ship to us we will come to you!</li>
      <li>Clear pricing upfront. No hidden cost.</li>
      <li>Next business-day repair.</li>
      <li>Backed by a professional call center open 12 hours a day and open on a Saturday as well</li>
    </ul>
    <ul>
      <li>Backed by a professional repair center with more than 12 years of experience</li>
      <li>Repair is done by certified engineers</li>
      <li>1 year warranty on the repair</li>
    </ul>
  </div>
  <span class="white-btn">REPAIR REQUEST</span>
</section>

<footer>
  <div class="site-footer">
    <div class="footer-brand"><span class="brand-mark"></span>Handset Haven</div>
    <div class="footer-col orders">
      <h4>ORDERS &amp; RETURNS</h4>
      <ul><li>Order Status</li><li>Shipping, Delivery &amp; Store Pickup</li><li>Return &amp; Exchange Promise</li><li>Price Match Guarantee</li><li>Pay With Points</li><li>Phone Orders &amp; Returns Help</li></ul>
    </div>
    <div class="footer-col contactus">
      <h4>CONTACT US</h4>
      <div class="contact-item"><svg width="14" height="18" viewBox="0 0 14 18"><path d="M7 17S1 10 1 6a6 6 0 0 1 12 0c0 4-6 11-6 11z" fill="#f26522"/></svg><div><b>ADDRESS</b>Havenkade 14<br>3011 AB Rotterdam</div></div>
      <div class="contact-item"><svg width="14" height="18" viewBox="0 0 14 18"><rect x="2" y="1" width="10" height="16" rx="2" fill="#f26522"/></svg><div><b>PHONE</b>010 555 0142</div></div>
      <div class="contact-item"><svg width="14" height="18" viewBox="0 0 14 18"><rect x="1" y="4" width="12" height="9" fill="#f26522"/></svg><div><b>Mail</b>info@handsethaven.com</div></div>
    </div>
    <div class="footer-col newsletter">
      <h4>NEWSLETTER SIGNUP</h4>
      <input type="text" value="Email address" aria-label="Email address">
      <br><span class="btn">SUBSCRIBE NOW</span>
    </div>
  </div>
  <div class="footer-bar">
    <span>Copyright © 2017 Handset Haven. All Rights Reserved.</span>
    <div class="socials" aria-label="Social media links"><span></span><span></span><span></span><span></span><span></span><span></span></div>
  </div>
</footer>

</body>
</html>
```